Looking for a modern, Professional business card design

We have a simple business card, but are looking for a more modern, professional look. A sample of the basic card is attached as well as the logo. We would also like to add that we offer:
Struggling with your finances?
- Learn to become debt free
- Discover the power of cash
- Control your money instead of it controlling you
Let us help you achieve a new level of financial freedom!
Also, we would like to have a "SPECIAL OFFER!: FREE 30 minute consultation"
Financial Planning

```html
<!DOCTYPE html>
<html lang="en">
<head>
<meta charset="utf-8">
<title>Clearpath Financial Coaching – Business Card</title>
<link rel="stylesheet" href="https://fonts.googleapis.com/css2?family=Open+Sans:ital,wght@0,400;0,600;0,700;0,800;1,600&display=swap">
<style>
  :root {
    --canvas-bg: #ecebea;
    --card-black: #231f20;
    --brand-green: #2c7a3a;
    --panel-green: #2e7d3c;
    --lime: #8dc63f;
    --edge-green: #6fb83a;
    --ink: #231f20;
    --white: #ffffff;
  }
  * { box-sizing: border-box; margin: 0; padding: 0; }
  html, body { width: 1200px; height: 900px; overflow: hidden; }
  body {
    background: var(--canvas-bg);
    font-family: "Open Sans", Arial, sans-serif;
    position: relative;
  }
  .card {
    position: absolute;
    overflow: hidden;
    box-shadow: 0 6px 18px rgba(0,0,0,0.18);
  }

  /* ---------- Front ---------- */
  .card-front {
    left: 238px; top: 62px; width: 555px; height: 342px;
    background: var(--card-black);
  }
  .card-front .panel { position: absolute; inset: 0; }
  .front-wordmark {
    position: absolute; left: 28px; top: 18px;
    font-size: 40px; font-weight: 800; letter-spacing: 1px; line-height: 1.2;
    color: var(--lime);
  }
  .identity {
    position: absolute; right: 27px; top: 70px; text-align: right;
    color: var(--white);
  }
  .identity .name { font-size: 20px; font-weight: 600; line-height: 1.3; }
  .identity .role { font-size: 15px; font-weight: 400; line-height: 1.3; }
  .contacts {
    position: absolute; right: 27px; top: 240px;
    list-style: none; text-align: right; color: var(--white);
    font-size: 15px; line-height: 20px;
  }
  .contacts li { display: flex; justify-content: flex-end; align-items: center; gap: 5px; }
  .contacts svg { width: 11px; height: 11px; fill: var(--white); }

  /* ---------- Back ---------- */
  .card-back {
    left: 459px; top: 518px; width: 559px; height: 343px;
    background: var(--white);
  }
  .brand-line {
    position: absolute; left: 38px; top: 52px;
    display: flex; align-items: center; gap: 10px;
  }
  .brand-line .brand-square {
    width: 16px; height: 16px; background: var(--lime);
  }
  .brand-line .brand-name {
    font-size: 24px; font-weight: 800; line-height: 1; color: var(--ink);
    letter-spacing: 0.3px;
  }
  .pitch {
    position: absolute; right: 20px; top: 140px; text-align: right;
  }
  .pitch .headline {
    font-size: 17px; font-weight: 600; color: var(--brand-green); margin-bottom: 13px;
  }
  .benefits { list-style: none; font-size: 15px; line-height: 20.5px; color: var(--ink); }
  .benefits li { display: flex; justify-content: flex-end; align-items: center; gap: 8px; }
  .benefits svg { width: 11px; height: 10px; fill: var(--brand-green); }
  .pitch .promise {
    margin-top: 12px; font-size: 15px; font-style: italic; font-weight: 600;
    color: var(--brand-green);
  }
  .offer-band {
    position: absolute; left: 0; right: 0; bottom: 0; height: 51px;
    background: var(--card-black); color: var(--lime);
    display: flex; align-items: center; justify-content: center;
    font-size: 17px; font-weight: 600;
  }
</style>
</head>
<body>

  <section class="card card-front" aria-label="Business card front">
    <svg class="panel" viewBox="0 0 555 342" preserveAspectRatio="none" aria-hidden="true">
      <polygon points="372,0 555,0 555,342 172,342" fill="var(--panel-green)"/>
      <polygon points="362,0 380,0 182,342 166,342" fill="var(--edge-green)"/>
    </svg>
    <div class="front-wordmark">CLEARPATH</div>
    <div class="identity">
      <p class="name">Daniel R. Hayes</p>
      <p class="role">Personal financial coach</p>
    </div>
    <ul class="contacts">
      <li>(555) 014-2297
        <svg viewBox="0 0 24 24" aria-hidden="true"><path d="M6.6 10.8a15 15 0 0 0 6.6 6.6l2.2-2.2a1 1 0 0 1 1-.25 11.4 11.4 0 0 0 3.6.57 1 1 0 0 1 1 1V20a1 1 0 0 1-1 1A17 17 0 0 1 3 4a1 1 0 0 1 1-1h3.5a1 1 0 0 1 1 1c0 1.25.2 2.45.57 3.57a1 1 0 0 1-.25 1z"/></svg>
      </li>
      <li>daniel@steadyledgercoach.com
        <svg viewBox="0 0 24 24" aria-hidden="true"><path d="M2 5h20v14H2z M3 6l9 7 9-7" stroke="var(--panel-green)" stroke-width="1.5"/></svg>
      </li>
      <li>www.steadyledgercoach.com
        <svg viewBox="0 0 24 24" aria-hidden="true"><circle cx="12" cy="12" r="11"/><path d="M1 12h22M12 1c4 4 4 18 0 22M12 1c-4 4-4 18 0 22" stroke="var(--panel-green)" stroke-width="1.5" fill="none"/></svg>
      </li>
    </ul>
  </section>

  <section class="card card-back" aria-label="Business card back">
    <div class="brand-line">
      <span class="brand-square" aria-hidden="true"></span>
      <p class="brand-name">CLEARPATH FINANCIAL COACHING</p>
    </div>
    <div class="pitch">
      <p class="headline">STRUGGLING WITH YOUR FINANCES?</p>
      <ul class="benefits">
        <li>Learn to become debt free <svg viewBox="0 0 11 10" aria-hidden="true"><polygon points="0,5 11,0 11,10"/></svg></li>
        <li>Discover the power of cash <svg viewBox="0 0 11 10" aria-hidden="true"><polygon points="0,5 11,0 11,10"/></svg></li>
        <li>Control your money instead of it controlling you <svg viewBox="0 0 11 10" aria-hidden="true"><polygon points="0,5 11,0 11,10"/></svg></li>
      </ul>
      <p class="promise">Let us help you achieve a new level of financial freedom!</p>
    </div>
    <div class="offer-band">SPECIAL OFFER!: FREE 30 MINUTE CONSULTATION</div>
  </section>

</body>
</html>
```